Business Card for a New Zealand IT Startup

I need a business card for VELTA Holdings. We are a young startup based in New Zealand working in internet marketing and web development. The design should have some element connected to New Zealand, such as wave, koru or silver fern, just don't use a kiwi bird.

```html
<!DOCTYPE html>
<html lang="en">
<head>
<meta charset="utf-8">
<title>VELTA Holdings — Business Card</title>
<link rel="stylesheet" href="https://fonts.googleapis.com/css2?family=Montserrat:wght@600;700&family=Open+Sans:ital,wght@0,400;0,600;1,400&display=swap">
<style>
  :root {
    --backdrop: #4a3f39;
    --card: #1b1c1f;
    --silver: #cfd0d2;
    --white: #f4f4f4;
    --blue: #1f7fd0;
    --orange: #ef6a2c;
  }
  * { box-sizing: border-box; margin: 0; padding: 0; }
  html, body { width: 1200px; height: 864px; overflow: hidden; }
  body {
    background: var(--backdrop);
    display: flex;
    align-items: center;
    justify-content: center;
    gap: 36px;
    font-family: "Open Sans", Arial, sans-serif;
  }
  .card {
    position: relative;
    width: 560px;
    height: 320px;
    background: var(--card);
    border-radius: 3px;
    box-shadow: 0 10px 24px rgba(0,0,0,.35);
    overflow: hidden;
  }

  /* Front */
  .front-brand {
    position: absolute;
    left: 70px;
    top: 92px;
    display: flex;
    align-items: center;
    gap: 16px;
  }
  .brand-name {
    font-family: "Montserrat", Arial, sans-serif;
    font-weight: 700;
    letter-spacing: 3px;
    line-height: 1;
  }
  .front-brand .brand-name { color: var(--silver); font-size: 40px; }
  .brand-dot { width: 34px; height: 34px; border-radius: 50%; }
  .front-brand .brand-dot { background: var(--silver); }
  .front-url {
    position: absolute;
    left: 72px;
    top: 196px;
    color: var(--silver);
    font-size: 15px;
    letter-spacing: 6px;
  }

  /* Back */
  .back-brand {
    position: absolute;
    right: 34px;
    top: 68px;
    display: flex;
    align-items: center;
    gap: 12px;
  }
  .back-brand .brand-name { color: var(--blue); font-size: 28px; }
  .back-brand .brand-dot { width: 26px; height: 26px; background: var(--blue); }

  .person { position: absolute; left: 34px; top: 92px; }
  .person-name {
    font-family: "Montserrat", Arial, sans-serif;
    font-weight: 700;
    color: var(--blue);
    font-size: 19px;
  }
  .person-title { color: var(--orange); font-size: 13px; letter-spacing: .5px; }

  .divider {
    position: absolute;
    left: 34px;
    right: 34px;
    top: 150px;
    height: 2px;
    background: var(--white);
  }

  .contacts {
    position: absolute;
    left: 34px;
    top: 164px;
    list-style: none;
    color: var(--white);
    font-size: 15px;
    line-height: 25px;
  }
  .contacts li { display: flex; align-items: center; gap: 9px; }
  .contacts svg { width: 14px; height: 14px; fill: var(--blue); flex: none; }

  .address {
    position: absolute;
    right: 34px;
    top: 214px;
    text-align: right;
    color: var(--white);
    font-size: 15px;
    line-height: 23px;
  }
</style>
</head>
<body>

  <section class="card card-front" aria-label="Card front">
    <div class="front-brand">
      <span class="brand-name">VELTA HOLDINGS</span>
      <span class="brand-dot"></span>
    </div>
    <p class="front-url">www.veltaholdings.com</p>
  </section>

  <section class="card card-back" aria-label="Card back">
    <div class="back-brand">
      <span class="brand-name">VELTA HOLDINGS</span>
      <span class="brand-dot"></span>
    </div>

    <div class="person">
      <p class="person-name">MARA QUILL</p>
      <p class="person-title">PRESIDENT</p>
    </div>

    <div class="divider"></div>

    <ul class="contacts">
      <li>
        <svg viewBox="0 0 16 16" aria-hidden="true"><path d="M3 1h3l1.5 4-2 1.2a9 9 0 0 0 4.3 4.3L11 8.5l4 1.5v3a2 2 0 0 1-2 2A12 12 0 0 1 1 3a2 2 0 0 1 2-2z"/></svg>
        555 0142 7781
      </li>
      <li>
        <svg viewBox="0 0 16 16" aria-hidden="true"><path d="M4.5 0h7A1.5 1.5 0 0 1 13 1.5v13a1.5 1.5 0 0 1-1.5 1.5h-7A1.5 1.5 0 0 1 3 14.5v-13A1.5 1.5 0 0 1 4.5 0zM5 2v10h6V2zm3 11a1 1 0 1 0 0 2 1 1 0 0 0 0-2z"/></svg>
        555 0198 3364
      </li>
      <li>
        <svg viewBox="0 0 16 16" aria-hidden="true"><path d="M4 1h8v4H4zM2 6h12a1 1 0 0 1 1 1v5h-3v3H4v-3H1V7a1 1 0 0 1 1-1zm3 5v3h6v-3z"/></svg>
        555 0176 2249
      </li>
      <li>
        <svg viewBox="0 0 16 16" aria-hidden="true"><path d="M1 3h14v1.2L8 9 1 4.2zm0 2.8 7 4.8 7-4.8V13H1z"/></svg>
        mara@veltaholdings.com
      </li>
    </ul>

    <address class="address" style="font-style: normal;">
      27 Kestrel Road<br>
      Ashford Bay, NZ 3110<br>
      www.veltaholdings.com
    </address>
  </section>

</body>
</html>
```